New Business Card Design Project

I need a design for business cards, i am an electrical business called "Corvane Electrical and Communications" i need the cards to be double sided with the company logo on the back (attached) the front needs to say my company name, web site, email address, telephone number, and ABN number and electrical license number. I am open to different arrangements of the information but would like the background to be incorporating something electrical or something that looks smart. open to all additional ideas also.

The company colours are orange and grey see logo attached.

Business Name: Corvane Electrical and Communications
Website: corvaneelectricalandcomms.example.com.au
Email: brent@corvaneelectricalandcomms.example.com.au
Telephone(mobile): 0481209736
ABN: 71208349162
Lic No: 418273D

Target Market(s)

Business entities, Project Managers, Accounts, Clients

Industry/Entity Type

Electrician

Contact Information for Business Card

I need a design for business cards, i am an electrical business called "Corvane Electrical and Communications" i need the cards to be double sided with the company logo on the back (attached) the front needs to say my company name

Font styles to use
Serif
Sans Serif

Colors
f37122
5c5c5c

Requirements
Must have
• Must have the Logo on the back open to different ways of it being on the back but had in mind to keep it central but again open to other options
Nice to have
• A real modern cool background that is eye catching yet contemporary
Should not have
• No backgrounds of a light bulb or plug or anything like that

```html
<!DOCTYPE html>
<html lang="en">
<head>
<meta charset="utf-8">
<title>Corvane Electrical and Communications – Business Card</title>
<link rel="stylesheet" href="https://fonts.googleapis.com/css2?family=Open+Sans:wght@400;600;700&display=swap">
<style>
  :root {
    --backdrop: #2b2c2f;
    --card-grey: #545456;
    --card-orange: #f9ab17;
    --accent-orange: #f9ab17;
    --ink-dark: #1a1a1a;
    --ink-light: #ffffff;
  }
  * { margin: 0; padding: 0; box-sizing: border-box; }
  html, body {
    width: 1200px;
    height: 864px;
    overflow: hidden;
  }
  body {
    background: var(--backdrop);
    font-family: "Open Sans", Arial, sans-serif;
    position: relative;
  }
  .card {
    position: absolute;
    width: 600px;
    height: 345px;
    border-radius: 2px;
    box-shadow: 0 10px 30px rgba(0, 0, 0, 0.35);
  }

  /* Back of card: company name */
  .card-back {
    left: 200px;
    top: 60px;
    background: var(--card-grey);
    display: flex;
    flex-direction: column;
    align-items: center;
    justify-content: center;
    gap: 34px;
  }
  .brand {
    display: flex;
    align-items: center;
    gap: 14px;
  }
  .brand-dot {
    width: 22px;
    height: 22px;
    border-radius: 50%;
    background: var(--accent-orange);
    flex: none;
  }
  .brand-name {
    color: var(--ink-light);
    font-weight: 700;
    font-size: 25px;
    letter-spacing: 0.2px;
  }
  .back-website {
    color: var(--ink-light);
    font-weight: 600;
    font-size: 15px;
  }

  /* Front of card: contact details */
  .card-front {
    left: 300px;
    top: 455px;
    background: var(--card-orange);
    color: var(--ink-dark);
    text-align: center;
    padding-top: 44px;
  }
  .person-name {
    font-weight: 700;
    font-size: 19px;
    line-height: 1.2;
  }
  .person-role {
    font-size: 13px;
    margin-top: 2px;
  }
  .registration {
    margin-top: 24px;
    font-weight: 700;
    font-size: 15px;
    line-height: 1.35;
  }
  .contact {
    margin-top: 24px;
    list-style: none;
    font-size: 15px;
    line-height: 1.35;
  }
  .label { font-weight: 700; }
</style>
</head>
<body>

  <section class="card card-back" aria-label="Business card back">
    <div class="brand">
      <span class="brand-dot" aria-hidden="true"></span>
      <span class="brand-name">Corvane Electrical and Communications</span>
    </div>
    <p class="back-website">corvaneelectricalandcomms.example.com.au</p>
  </section>

  <section class="card card-front" aria-label="Business card front">
    <h1 class="person-name">Brent Marlow</h1>
    <p class="person-role">Director</p>

    <p class="registration">
      ABN: 71208349162<br>
      Lic No: 418273D
    </p>

    <ul class="contact">
      <li><span class="label">Phone:</span> 0481209736</li>
      <li><span class="label">Email:</span> brent@corvaneelectricalandcomms.example.com.au</li>
      <li><span class="label">Website:</span> corvaneelectricalandcomms.example.com.au</li>
    </ul>
  </section>

</body>
</html>
```